Business card for a new cabinet shop company named Veloran Cabinets for high end cabinets

Design a business card, thinking dark rich green with colours to speak of high end luxury ie; cream, gold, black possibly

Mitchell Tarrowby
Director Craftsman
Email: info@veloranjoinery-example.com.au
Instagram : @veloran.cabinets

```html
<!DOCTYPE html>
<html lang="en">
<head>
<meta charset="utf-8">
<title>Veloran Cabinets – Business Card</title>
<link href="https://fonts.googleapis.com/css2?family=Montserrat:wght@400;500;700&display=swap" rel="stylesheet">
<style>
  :root {
    --backdrop: #161616;
    --card-green: #1f3d3b;
    --pattern-green: #2a504c;
    --gold: #c9a463;
    --cream: #f1efe8;
  }
  * { margin: 0; padding: 0; box-sizing: border-box; }
  html, body {
    width: 1200px;
    height: 1059px;
    overflow: hidden;
    background: var(--backdrop);
    font-family: "Montserrat", sans-serif;
  }
  .card {
    position: absolute;
    border-radius: 26px;
    background: var(--card-green);
    overflow: hidden;
  }
  .card--front { left: 259px; top: 102px; width: 690px; height: 394px; }
  .card--back { left: 257px; top: 547px; width: 697px; height: 398px; }

  .brand {
    position: absolute;
    display: flex;
    align-items: center;
    gap: 14px;
    color: var(--gold);
    font-weight: 500;
    white-space: nowrap;
  }
  .brand__mark {
    border: 2px solid var(--gold);
    border-radius: 4px;
  }
  .card--front .brand { right: 43px; top: 82px; font-size: 34px; }
  .card--front .brand__mark { width: 42px; height: 42px; }
  .card--back .brand { right: 78px; top: 225px; font-size: 26px; }
  .card--back .brand__mark { width: 32px; height: 32px; }

  .holder { position: absolute; left: 45px; top: 203px; }
  .holder__name {
    color: var(--gold);
    font-weight: 700;
    font-size: 26px;
    line-height: 32px;
  }
  .holder__role {
    color: var(--cream);
    font-weight: 400;
    font-size: 19px;
    line-height: 24px;
    margin-top: 6px;
  }
  .divider {
    position: absolute;
    left: 46px;
    width: 601px;
    top: 279px;
    height: 2px;
    background: var(--cream);
  }
  .contact {
    position: absolute;
    display: flex;
    align-items: center;
    gap: 9px;
    color: var(--cream);
    font-size: 19px;
    line-height: 24px;
    white-space: nowrap;
  }
  .contact svg { flex: none; fill: var(--gold); }
  .contact--email { left: 43px; top: 300px; }
  .contact--place { left: 44px; top: 333px; }
  .contact--social { right: 43px; top: 330px; }
  .social-dot {
    width: 16px; height: 16px;
    border: 2px solid var(--gold);
    border-radius: 50%;
  }

  .pattern-field {
    position: absolute;
    inset: 0;
    background:
      radial-gradient(ellipse at 30% 40%, var(--pattern-green), transparent 70%),
      linear-gradient(135deg, var(--card-green), var(--pattern-green) 50%, var(--card-green));
  }
</style>
</head>
<body>

<section class="card card--front">
  <div class="brand"><span class="brand__mark"></span>Veloran Cabinets</div>

  <div class="holder">
    <h1 class="holder__name">Mitchell Tarrowby</h1>
    <p class="holder__role">Director Craftsman</p>
  </div>

  <div class="divider"></div>

  <p class="contact contact--email">
    <svg width="18" height="13" viewBox="0 0 18 13" aria-hidden="true">
      <path d="M0 0h18v1.5L9 7 0 1.5z"/><path d="M0 3.5 9 9l9-5.5V13H0z"/>
    </svg>
    info@veloranjoinery-example.com.au
  </p>
  <p class="contact contact--place">
    <svg width="16" height="20" viewBox="0 0 16 20" aria-hidden="true">
      <path d="M8 0a8 8 0 0 0-8 8c0 5.5 8 12 8 12s8-6.5 8-12a8 8 0 0 0-8-8zm0 11a3 3 0 1 1 0-6 3 3 0 0 1 0 6z"/>
    </svg>
    Kestrelvale Coast
  </p>
  <p class="contact contact--social">
    <span class="social-dot"></span>
    @veloran.cabinets
  </p>
</section>

<section class="card card--back">
  <div class="pattern-field" role="img" aria-label="Repeating tonal pattern of the brand symbol in muted green across the whole card back"></div>
  <div class="brand"><span class="brand__mark"></span>Veloran Cabinets</div>
</section>

</body>
</html>
```